Therapeutic Counselling Practice Brochure

I have a new therapeutic counselling practice in Melbourne.

I am making peri natal issues my special interest area.

I need a brochure targeted at new parents or pregnant women and partners, struggling with the concept of parenting, depression, maybe do not even know about it.

The feel should be safe and strong. I love the WREN website ( I do volunteer work with them)

Out of hours appointments and telephone counselling are important making my service very accessible.

Attached is an example for the content of the Brochure

Attached is an example for the content of the Brochure.

Target Market(s)

25 - 45 New Parents , expectant parents,families and friends of people struggling emotionally and mentally with and around being new parents

Requirements
Must have
• Feel of safety, somewhere to go for help, support, a conversation, soft ,strong
Nice to have
• mother and child, maybe parents and child, possibly a graphic, faceless

```html
<!DOCTYPE html>
<html lang="en">
<head>
<meta charset="utf-8">
<title>Maren Holloway – Counsellor and Personal Coach brochure</title>
<link rel="stylesheet" href="https://fonts.googleapis.com/css2?family=Open+Sans:ital,wght@0,400;0,600;0,700;1,400;1,700&family=Arimo:ital,wght@0,400;0,700;1,700&display=swap">
<style>
  :root {
    --green-deep: #3c6a1c;
    --green-mid: #5f9b2a;
    --green-bright: #8cc13a;
    --green-light: #b9d96a;
    --green-pale: #eef5dc;
    --ink: #2b2b2b;
    --paper: #ffffff;
    --backdrop: #ece9e3;
  }
  * { box-sizing: border-box; margin: 0; padding: 0; }
  html, body { width: 1200px; height: 740px; overflow: hidden; }
  body {
    background: var(--backdrop);
    font-family: "Open Sans", Arial, sans-serif;
    color: var(--ink);
    position: relative;
  }
  .panel {
    position: absolute;
    top: 30px;
    width: 370px;
    height: 680px;
    background: var(--paper);
    overflow: hidden;
    box-shadow: 0 2px 8px rgba(0,0,0,.15);
  }
  .panel--article { left: 25px; }
  .panel--contact { left: 415px; }
  .panel--cover   { left: 805px; }
  .curve { position: absolute; left: 0; width: 100%; display: block; }

  /* Article panel */
  .article-head {
    position: absolute; top: 0; left: 0; width: 100%; height: 210px;
    background: linear-gradient(180deg, var(--green-pale), #f9fcf1);
  }
  .article-photo {
    position: absolute; top: 28px; right: 0; width: 120px; height: 150px;
    background: linear-gradient(180deg, #d9b98a 0%, #8f7a62 55%, #3d3a35 100%);
  }
  .article-title {
    position: absolute; top: 38px; left: 28px; width: 240px;
    color: var(--green-deep); font-family: "Open Sans", sans-serif; line-height: 1.1;
  }
  .article-title .big { display: block; font-size: 33px; font-weight: 700; letter-spacing: .5px; }
  .article-title .line { display: block; font-size: 22px; font-weight: 400; margin-top: 3px; }
  .article-title b { font-weight: 700; }
  .article-body {
    position: absolute; top: 232px; left: 28px; right: 24px;
    font-size: 11.2px; line-height: 1.42; text-align: justify;
  }
  .article-body p { margin-bottom: 10px; }
  .highlight { color: var(--green-mid); font-weight: 600; }
  .article-link {
    display: block; text-align: right; color: var(--green-mid);
    font-size: 15px; font-weight: 600; margin-top: -4px;
  }

  /* Contact panel */
  .portrait {
    position: absolute; top: 0; left: 0; width: 100%; height: 205px;
    background: linear-gradient(120deg, #f3efe8 0%, #e6d6c6 45%, #9fbf6a 80%, #5f8c35 100%);
  }
  .name-tab {
    position: absolute; top: 200px; left: 0; width: 100%; height: 34px;
  }
  .name-tab span {
    position: absolute; left: 36px; top: 10px;
    font-size: 12px; font-weight: 700; color: var(--green-deep);
  }
  .contact-body {
    position: absolute; top: 252px; left: 28px; right: 26px;
    font-size: 12px; line-height: 1.45;
  }
  .contact-body p { margin-bottom: 12px; }
  .contact-body strong { font-weight: 700; }
  .contact-body em { font-style: italic; }
  .booking { text-align: center; margin-top: 6px; font-size: 11.5px; line-height: 1.45; }

  /* Cover panel */
  .cover-band {
    position: absolute; top: 0; left: 0; width: 100%; height: 120px;
    background: linear-gradient(180deg, var(--green-deep), var(--green-mid));
  }
  .brand {
    position: absolute; top: 26px; left: 28px; display: flex; align-items: center; gap: 12px;
    color: var(--paper); font-family: "Arimo", Arial, sans-serif; font-weight: 700;
  }
  .brand-mark { width: 36px; height: 36px; border-radius: 50%; border: 2px solid var(--paper); }
  .brand-name { font-size: 21px; line-height: 1.1; }
  .brand-role { font-size: 12.5px; line-height: 1.2; }
  .cover-photo {
    position: absolute; top: 118px; left: 0; width: 100%; height: 300px;
    background: linear-gradient(100deg, #c9794e 0%, #e9b99b 40%, #f4ddd0 70%, #fbf3ee 100%);
  }
  .cover-headline {
    position: absolute; top: 430px; left: 24px; right: 14px;
    font-family: "Arimo", Arial, sans-serif;
  }
  .cover-headline h2 { font-size: 23px; font-weight: 700; color: var(--green-deep); line-height: 1.15; letter-spacing: .3px; }
  .cover-headline h3 { font-size: 19px; font-style: italic; font-weight: 700; color: var(--green-bright); margin-top: 2px; }
  .cover-lower {
    position: absolute; top: 505px; left: 0; width: 100%; height: 175px;
  }
  .cover-text {
    position: absolute; top: 528px; left: 26px; right: 22px;
    font-family: "Arimo", Arial, sans-serif; font-size: 12.5px; line-height: 1.3; color: var(--paper);
  }
</style>
</head>
<body>

  <section class="panel panel--article">
    <div class="article-head"></div>
    <div class="article-photo" role="img" aria-label="Sunset silhouette of a father holding his child"></div>
    <h1 class="article-title">
      <span class="big">DEPRESSION</span>
      <span class="line">in <b>Men</b> after the</span>
      <span class="line"><b>Birth</b> of their <b>Baby</b></span>
    </h1>
    <svg class="curve" style="top:196px" height="30" viewBox="0 0 370 30" preserveAspectRatio="none">
      <path d="M0 14 Q185 2 370 10 L370 30 L0 30 Z" fill="var(--paper)"/>
      <path d="M0 14 L24 10 L24 26 L0 28 Z" fill="var(--green-light)"/>
    </svg>
    <div class="article-body">
      <p>Becoming a father can be difficult to cope with and some men feel they have nowhere to turn for support.</p>
      <p>According to recent research, about <span class="highlight">10 per cent of new fathers</span> become depressed after the birth of their child.</p>
      <span class="article-link">www.kestrelfathers.org.uk</span>
      <p>Having a new baby is a huge change, involving physical exhaustion and extra worries. It can be particularly difficult to balance the demands of work and fatherhood, especially as you might feel under pressure to earn more while your partner is not able to work.</p>
      <p>For new parents the focus of attention will have shifted and this can feel like a loss as well as a gain.</p>
      <p>Some men report feeling overwhelmed, isolated and confused by their feelings and their partner's reaction to them. They are often irritable, aggressive and sometimes hostile. Symptoms can include feeling very low - for example, not enjoying anything, poor concentration, perhaps a poor appetite and worrying at night. Some men feel ashamed of their feelings and experiences and this makes it very difficult for them to seek out and receive help.</p>
      <p>Counselling can help, being able to talk openly and honestly in a safe and confidential space.</p>
    </div>
    <svg class="curve" style="bottom:0" height="60" viewBox="0 0 370 60" preserveAspectRatio="none">
      <path d="M0 30 Q200 10 370 24 L370 60 L0 60 Z" fill="var(--green-light)"/>
      <path d="M0 42 Q200 24 370 38 L370 60 L0 60 Z" fill="var(--green-bright)"/>
    </svg>
  </section>

  <section class="panel panel--contact">
    <div class="portrait" role="img" aria-label="Portrait photograph of the counsellor beside green foliage"></div>
    <svg class="name-tab" viewBox="0 0 370 34" preserveAspectRatio="none">
      <path d="M0 6 L370 0 L370 34 L0 34 Z" fill="var(--paper)"/>
      <path d="M20 8 L180 4 L180 30 L20 32 Z" fill="var(--green-light)"/>
    </svg>
    <div class="name-tab"><span>Maren Holloway J.P.</span></div>
    <div class="contact-body">
      <p><strong>Office:</strong><br>Level 2, 48 Larkfield Street,<br>Southbank 3006</p>
      <p><em>Evening and weekend appointments available.</em></p>
      <p><strong>Telephone Counselling</strong> saves travel time and the hassle of parking.</p>
      <p>Telephone counselling gives you a convenient option in accessing therapy.</p>
      <p>Some people feel more comfortable discussing issues over the telephone, still within the safe supportive and confidential framework.</p>
      <p><strong><em>Telephone appointments are usually available within 48 hours.</em></strong></p>
      <div class="booking">To book please contact<br>Maren Holloway<br>on 0400 123 456<br>maren@marenholloway.com.au<br>www.marenholloway.com.au</div>
    </div>
    <svg class="curve" style="bottom:0" height="60" viewBox="0 0 370 60" preserveAspectRatio="none">
      <path d="M0 26 Q170 10 370 28 L370 60 L0 60 Z" fill="var(--green-light)"/>
      <path d="M0 40 Q170 24 370 42 L370 60 L0 60 Z" fill="var(--green-bright)"/>
    </svg>
  </section>

  <section class="panel panel--cover">
    <div class="cover-photo" role="img" aria-label="Photograph of a smiling mother holding her baby"></div>
    <div class="cover-band"></div>
    <svg class="curve" style="top:95px" height="50" viewBox="0 0 370 50" preserveAspectRatio="none">
      <path d="M0 0 L370 0 L370 12 Q190 26 0 46 Z" fill="var(--green-mid)"/>
      <path d="M0 46 Q190 26 370 12 L370 22 Q190 34 0 50 Z" fill="var(--green-light)"/>
    </svg>
    <div class="brand">
      <span class="brand-mark"></span>
      <div>
        <div class="brand-name">Maren Holloway</div>
        <div class="brand-role">Counsellor and Personal Coach</div>
      </div>
    </div>
    <svg class="curve" style="top:400px" height="30" viewBox="0 0 370 30" preserveAspectRatio="none">
      <path d="M0 30 Q180 0 370 18 L370 30 Z" fill="var(--paper)"/>
    </svg>
    <div class="cover-headline">
      <h2>ARE YOU EXPECTING<br>OR A NEW PARENT?</h2>
      <h3>Got the “Baby Blues”?</h3>
    </div>
    <svg class="cover-lower" viewBox="0 0 370 175" preserveAspectRatio="none">
      <defs>
        <linearGradient id="coverGreen" x1="0" y1="0" x2="0" y2="1">
          <stop offset="0" stop-color="#6fae2e"/>
          <stop offset="1" stop-color="#3c6a1c"/>
        </linearGradient>
      </defs>
      <path d="M0 18 Q200 0 370 10 L370 175 L0 175 Z" fill="url(#coverGreen)"/>
      <path d="M0 140 Q200 110 370 128 L370 150 Q200 134 0 160 Z" fill="var(--green-light)"/>
      <path d="M0 160 Q200 134 370 150 L370 175 L0 175 Z" fill="var(--green-bright)"/>
    </svg>
    <p class="cover-text">There is an expectation of happiness and fulfilment around childbirth.<br>Feeling “blue”, interferes with the adjustment to becoming a parent.<br>Sharing your feelings by talking is important.</p>
  </section>

</body>
</html>
```